Graphic Design of Business Process

We require an eye-catching, sophisticated design of 2 business processes (attached), that will be used digitally AND for print (to be put on walls in our office).

The basic layout is attached. We require a creative, professional designer to re-design these so that they look appealing but still able to grasp all the information.

We will require vector files and editable project files for final delivery. You may refer to our website (quillharbourworks.com.au) for an indication of our brand.

If you have any questions, please ask.

Thank you.

```html
<!DOCTYPE html>
<html lang="en">
<head>
<meta charset="utf-8">
<title>Content Hierarchy</title>
<link rel="stylesheet" href="https://fonts.googleapis.com/css2?family=Montserrat:wght@800&family=Oswald:wght@600&display=swap">
<style>
  :root {
    --ink: #0c0c0c;
    --sky-edge: #9fd8f4;
    --sky-mid: #dff1fb;
    --rule: #f9b43a;
    --card-frame: #e4e6e8;
    --hero: #4a56a8;
    --hero-deep: #394185;
    --hub: #bb4a9d;
    --hub-deep: #8f3a79;
    --hygiene: #fbb03b;
    --hygiene-deep: #b78640;
    --hygiene-text: #f29222;
  }
  * { box-sizing: border-box; margin: 0; padding: 0; }
  html, body { width: 1200px; height: 2579px; overflow: hidden; }
  body {
    position: relative;
    background: radial-gradient(ellipse 60% 55% at 50% 50%, #ffffff 0%, var(--sky-mid) 55%, var(--sky-edge) 100%);
    font-family: "Oswald", "Arial Narrow", sans-serif;
  }
  .headline {
    position: absolute; top: 92px; left: 0; width: 100%;
    text-align: center;
    font-family: "Montserrat", "Arial Black", sans-serif;
    font-weight: 800; font-size: 112px; line-height: 154px;
    letter-spacing: 2px; color: var(--ink);
  }
  .headline-rule {
    position: absolute; top: 398px; left: 226px; width: 746px; height: 17px;
    background: var(--rule);
  }
  .tier { position: absolute; left: 437px; width: 326px; }
  .tier svg { position: absolute; left: 0; top: 0; }
  .tier-name, .tier-role {
    position: absolute; left: 0; width: 100%;
    text-align: center; font-weight: 600; text-transform: uppercase;
  }
  .tier-name { font-size: 62px; line-height: 70px; }
  .tier-role { font-size: 50px; line-height: 79px; }
  .tier--hero { top: 459px; height: 624px; color: var(--hero); }
  .tier--hub { top: 1097px; height: 660px; color: var(--hub); }
  .tier--hygiene { top: 1774px; height: 656px; color: var(--hygiene-text); }
  .brand {
    position: absolute; top: 2452px; left: 843px; width: 300px;
    font-family: "Montserrat", "Arial Black", sans-serif;
    font-weight: 800; font-size: 22px; letter-spacing: 3px;
    color: var(--ink); text-align: center;
  }
</style>
</head>
<body>
  <h1 class="headline">CONTENT<br>HIERARCHY</h1>
  <div class="headline-rule"></div>

  <section class="tier tier--hero">
    <svg width="326" height="624" viewBox="0 0 326 624">
      <rect x="2.5" y="190" width="321" height="431.5" fill="#fff" stroke="var(--card-frame)" stroke-width="5"/>
      <rect x="8" y="599" width="310" height="19" fill="var(--hero)"/>
      <polygon points="163,0 326,94 326,296 163,390 0,296 0,94" fill="var(--hero)"/>
      <polygon points="163,20 309,104 309,286 163,370 17,286 17,104" fill="var(--hero-deep)"/>
      <polygon points="163,38 293,113 293,277 163,352 33,277 33,113" fill="#fff"/>
    </svg>
    <div class="tier-name" style="top:149px">Hero</div>
    <div class="tier-role" style="top:412px">Tentpole<br>Campaigns</div>
  </section>

  <section class="tier tier--hub">
    <svg width="326" height="660" viewBox="0 0 326 660">
      <rect x="2.5" y="190" width="321" height="467.5" fill="#fff" stroke="var(--card-frame)" stroke-width="5"/>
      <rect x="8" y="638" width="310" height="17" fill="var(--hub)"/>
      <polygon points="163,0 326,94 326,296 163,390 0,296 0,94" fill="var(--hub)"/>
      <polygon points="163,20 309,104 309,286 163,370 17,286 17,104" fill="var(--hub-deep)"/>
      <polygon points="163,38 293,113 293,277 163,352 33,277 33,113" fill="#fff"/>
    </svg>
    <div class="tier-name" style="top:154px">Hub</div>
    <div class="tier-role" style="top:395px">Regular<br>“Push”<br>Content</div>
  </section>

  <section class="tier tier--hygiene">
    <svg width="326" height="656" viewBox="0 0 326 656">
      <rect x="2.5" y="190" width="321" height="463.5" fill="#fff" stroke="var(--card-frame)" stroke-width="5"/>
      <rect x="8" y="634" width="310" height="19" fill="var(--hygiene-text)"/>
      <polygon points="163,0 326,94 326,296 163,390 0,296 0,94" fill="var(--hygiene)"/>
      <polygon points="163,20 309,104 309,286 163,370 17,286 17,104" fill="var(--hygiene-deep)"/>
      <polygon points="163,38 293,113 293,277 163,352 33,277 33,113" fill="#fff"/>
    </svg>
    <div class="tier-name" style="top:157px">Hygiene</div>
    <div class="tier-role" style="top:398px">Always-On<br>“Pull”<br>Content</div>
  </section>

  <div class="brand">QUILL HARBOUR WORKS</div>
</body>
</html>
```